Redesign of business card for Cedar Ridge Mechanical

We are looking for a new design for our business cards for Cedar Ridge Mechanical. We are a plumbing & HVAC construction company, operating on the West Coast of Canada and USA. Logo attached.
Industry/Entity Type
Construction - Plumbing & HVAC
Contact Information for Business Card
Name, address, phone numbers, email, website address
Look and feel
Each slider illustrates characteristics of the customer's brand and the style your logo design should communicate.

```html
<!DOCTYPE html>
<html lang="en">
<head>
<meta charset="utf-8">
<title>Cedar Ridge Mechanical – Business Card</title>
<link href="https://fonts.googleapis.com/css2?family=Montserrat:wght@400;700&display=swap" rel="stylesheet">
<style>
  :root {
    --ink: #0a0a0a;
    --paper: #ffffff;
    --stripe: #8a8a8a;
    --backdrop: #e7e7e9;
    --muted: #d9d9d9;
  }
  * { box-sizing: border-box; margin: 0; padding: 0; }
  html, body { width: 1200px; height: 913px; overflow: hidden; }
  body {
    background: var(--backdrop);
    font-family: "Montserrat", sans-serif;
    position: relative;
  }
  .card {
    position: absolute;
    width: 540px;
    height: 310px;
    border-radius: 22px;
    overflow: hidden;
    background: var(--paper);
    box-shadow: 0 10px 30px rgba(0,0,0,.18);
  }
  .card--front { left: 40px; top: 301px; }
  .card--back  { left: 620px; top: 301px; }

  .wordmark {
    display: flex;
    align-items: center;
    gap: 14px;
    color: var(--ink);
    font-weight: 700;
    text-transform: uppercase;
    letter-spacing: .04em;
    line-height: 1.1;
  }
  .wordmark__square {
    flex: none;
    border: 6px solid var(--ink);
    border-radius: 6px;
  }
  .card--front .wordmark {
    position: absolute; left: 0; right: 0; top: 0; bottom: 0;
    justify-content: center;
    font-size: 30px;
  }
  .card--front .wordmark__square { width: 62px; height: 62px; }

  .card--back .wordmark {
    position: absolute; right: 26px; top: 26px;
    font-size: 19px;
  }
  .card--back .wordmark__square { width: 42px; height: 42px; border-width: 5px; }

  .back-shape { position: absolute; left: 0; top: 0; }

  .contact {
    position: absolute;
    left: 34px;
    top: 118px;
    color: var(--paper);
  }
  .contact__name { font-size: 18px; font-weight: 700; letter-spacing: .04em; text-transform: uppercase; line-height: 22px; }
  .contact__role { font-size: 12px; line-height: 16px; color: var(--muted); margin-top: 2px; }
  .contact__address { font-size: 12px; line-height: 17px; color: var(--muted); margin-top: 12px; }
  .contact__list { list-style: none; margin-top: 12px; font-size: 12px; line-height: 20px; }
  .contact__list li { display: flex; align-items: center; gap: 8px; }
  .contact__list svg { width: 12px; height: 12px; fill: var(--paper); flex: none; }
</style>
</head>
<body>
  <section class="card card--front" aria-label="Card front">
    <div class="wordmark">
      <span class="wordmark__square"></span>
      <span>Cedar Ridge<br>Mechanical</span>
    </div>
  </section>

  <section class="card card--back" aria-label="Card back">
    <svg class="back-shape" width="540" height="310" viewBox="0 0 540 310">
      <path d="M0 84 C150 44 330 69 540 244 L540 310 L0 310 Z" fill="var(--stripe)"/>
      <path d="M0 95 C150 55 330 80 540 255 L540 310 L0 310 Z" fill="var(--ink)"/>
    </svg>
    <div class="wordmark">
      <span class="wordmark__square"></span>
      <span>Cedar Ridge<br>Mechanical</span>
    </div>
    <div class="contact">
      <p class="contact__name">Daniel Hayes</p>
      <p class="contact__role">Managing Director</p>
      <p class="contact__address">Your address, City<br>State, Zip 1234</p>
      <ul class="contact__list">
        <li><svg viewBox="0 0 12 12"><path d="M2.5 1 4.5 3.2 3.6 4.6c.7 1.5 2 2.8 3.8 3.8l1.4-.9L11 9.5 9.6 11C5 10.4 1.6 7 1 2.4Z"/></svg>123 456 789</li>
        <li><svg viewBox="0 0 12 12"><path d="M1 3h10v6.5H1Zm1 .8 4 3 4-3V4.6L6 7.6 2 4.6Z"/></svg>info@yourgmail.com</li>
        <li><svg viewBox="0 0 12 12"><circle cx="6" cy="6" r="5"/></svg>www.yourwebsite.com</li>
      </ul>
    </div>
  </section>
</body>
</html>
```